WP website design for Kemble

We need a wordpress design that will incorporate a professional color scheme with company logo in a clean layout. The design needs to consider that this will be developed on a responsive theme. Colors are will be the green of the logo and any others that will creatively highlight it.

Industry/Entity Type

It Company

Font styles to use
Sans Serif

Requirements
Must have
• Navigation: 1) Home 2) Auctions 3) Auction Services 4) Sellers 5) TR Kemble Livestock 6) About Us 7) Contact Us
Site will have slideshow element, image attached.
Widgets will be: 1)Email Signup form 2) Featured Auctions widget 3) Social Media (FB, Youtube, RSS) 4) News & Events blog
Footer will have smaller company logo, association logos (attached) and contact info (below)
▪ T.R. Kemble Inc. / Auctioneers
▪ 4710 NC Hwy 91
▪ Cedar Ridge, NC 27000
▪ Office: (555) 318-6402
▪ Cell: (555) 274-8813
▪ email: trkemble@trkemble-example.com
Nice to have
• Site will have drop-down menus - please indicate the styling, for instance the dropdown menus

```html
<!DOCTYPE html>
<html lang="en">
<head>
<meta charset="utf-8">
<title>T.R. Kemble Inc. / Auctioneers</title>
<link href="https://fonts.googleapis.com/css2?family=Open+Sans:wght@300;400;600&display=swap" rel="stylesheet">
<style>
:root{
  --green:#3b8a1c;
  --green-text:#3a8a1f;
  --green-button:#6ab04c;
  --nav-active:#3a3a3a;
  --ink:#333;
  --body-text:#666;
  --soft-bg:#f4f4f4;
  --band:#dcdcdc;
  --footer:#2b2b2b;
  --footer-text:#bbb;
  --date-box:#5a5a5a;
}
*{margin:0;padding:0;box-sizing:border-box}
html,body{width:758px;height:1200px;overflow:hidden;background:#fff}
body{font-family:'Open Sans',sans-serif;color:var(--ink);position:relative}
.abs{position:absolute}
.site-header{left:0;top:0;width:758px;height:104px;background:#fff}
.brand{left:64px;top:30px;display:flex;align-items:center;gap:8px}
.brand-mark{width:18px;height:18px;border-radius:50%;background:var(--green)}
.brand-name{font-size:18px;font-weight:600;color:var(--green-text);line-height:1.1}
.brand-name small{display:block;font-size:12px;font-weight:600}
.header-contact{right:88px;top:33px;text-align:right}
.header-contact .address{font-size:9.5px;color:#777}
.header-contact .phone{font-size:13px;color:#333;margin-top:3px}
.header-contact .phone b{font-weight:600;color:var(--green-text)}
.contact-icon{left:680px;top:40px}
.main-nav{left:0;top:104px;width:758px;height:33px;background:var(--green)}
.main-nav a{position:absolute;top:0;height:33px;line-height:33px;font-size:9.5px;color:#fff;text-decoration:none;text-transform:uppercase}
.main-nav a.current{background:var(--nav-active);padding:0 17px}
.hero{left:0;top:137px;width:758px;height:317px;background:linear-gradient(180deg,#c7d8e8 0%,#9c8a66 35%,#b98f4f 55%,#8b7a5a 72%,#c7d3dc 100%)}
.hero-arrow{top:142px;width:26px;height:34px;background:rgba(30,30,30,.75)}
.hero-caption{left:0;width:758px;top:256px;text-align:center;font-size:22px;color:#fff;text-shadow:0 2px 4px rgba(0,0,0,.6)}
.welcome{left:0;top:454px;width:758px;height:152px;text-align:center}
.welcome h1{font-weight:400;font-size:19px;color:var(--green-text);margin-top:27px}
.welcome p{width:566px;margin:6px auto 0;font-size:9.6px;line-height:16px;color:var(--body-text)}
.widgets{left:0;top:606px;width:758px;height:398px;background:var(--soft-bg)}
.widget-title{font-weight:400;font-size:15px;color:var(--green-text)}
.auction-card{width:90px;height:96px;background:#fff}
.auction-card .photo{width:90px;height:70px}
.auction-card .label{height:26px;line-height:26px;text-align:center;font-size:8.5px;color:#666}
.post-list{width:292px;background:#fff}
.post{position:absolute;left:8px;width:276px}
.date{position:absolute;left:0;top:0;width:40px;height:53px;background:var(--date-box);color:#fff;text-align:center}
.date .m{font-size:9px;display:block;margin-top:12px;line-height:10px}
.date .d{font-size:15px;font-weight:600;line-height:18px}
.post p{position:absolute;left:49px;top:0;width:220px;font-size:8.4px;line-height:13px;color:#666}
.newsletter{left:0;top:1004px;width:758px;height:64px;background:var(--band)}
.newsletter h2{position:absolute;left:107px;top:17px;font-weight:300;font-size:19px;color:var(--green-text)}
.field{position:absolute;top:21px;height:22px;background:#fff;border:1px solid #e2e2e2;font-size:9.5px;line-height:20px;padding-left:9px;color:#333}
.subscribe{position:absolute;left:587px;top:21px;width:63px;height:22px;background:var(--green-button);color:#fff;font-size:10px;line-height:22px;text-align:center;border-radius:2px}
.site-footer{left:0;top:1068px;width:758px;height:132px;background:var(--footer)}
.footer-nav{position:absolute;top:14px;left:0;width:758px;text-align:center;font-size:8.8px;color:var(--footer-text)}
.footer-nav span{margin:0 10px}
.footer-nav span::before{content:"•";font-size:6px;margin-right:3px;vertical-align:middle}
.footer-rule{position:absolute;left:64px;top:41px;width:632px;height:1px;background:#444}
.copyright{position:absolute;left:64px;top:58px;font-size:8.8px;color:var(--footer-text)}
.footer-brand{position:absolute;left:64px;top:82px;font-size:10px;font-weight:600;color:#8a8a8a;line-height:1.2}
.footer-contact{position:absolute;right:63px;top:62px;text-align:right;font-size:8.8px;line-height:20.5px;color:var(--footer-text)}
</style>
</head>
<body>
<header class="site-header abs">
  <div class="brand abs"><span class="brand-mark"></span><span class="brand-name">T.R. Kemble<small>Inc. / Auctioneers</small></span></div>
  <div class="header-contact abs">
    <div class="address">4710 NC Hwy 91, Cedar Ridge, NC 27000</div>
    <div class="phone">Call us : <b>(555) 318-6402</b></div>
  </div>
  <svg class="contact-icon abs" width="16" height="20" viewBox="0 0 16 20"><rect x="1" y="1" width="13" height="18" rx="1" fill="none" stroke="#555" stroke-width="1.4"/><rect x="14" y="4" width="2" height="2" fill="#555"/><rect x="14" y="9" width="2" height="2" fill="#555"/><rect x="14" y="14" width="2" height="2" fill="#555"/><circle cx="7.5" cy="10" r="3" fill="none" stroke="#555" stroke-width="1.2"/></svg>
</header>

<nav class="main-nav abs">
  <a class="current" style="left:63px">Home</a>
  <a style="left:142px">Auctions</a>
  <a style="left:222px">Auction Services</a>
  <a style="left:340px">Sellers</a>
  <a style="left:410px">TR Kemble Livestock</a>
  <a style="left:540px">About Us</a>
  <a style="left:620px">Contact Us</a>
</nav>

<section class="hero abs" role="img" aria-label="Slideshow photo: autumn trees and golden meadow reflected in a pond">
  <svg class="hero-arrow abs" style="left:0" viewBox="0 0 26 34"><path d="M16 9 L9 17 L16 25" fill="none" stroke="#fff" stroke-width="1.4"/></svg>
  <svg class="hero-arrow abs" style="right:0" viewBox="0 0 26 34"><path d="M10 9 L17 17 L10 25" fill="none" stroke="#fff" stroke-width="1.4"/></svg>
  <div class="hero-caption abs">North Carolina Auctions and Auctioneering</div>
</section>

<section class="welcome abs">
  <h1>Welcome to T.R. Kemble, Inc</h1>
  <p>Mauris egestas, mi nec rutrum laoreet, nisi nibh scelerisque orci, a vehicula enim libero vel dui. Aenean quam nisi, feugiat id elit eu, convallis accumsan mauris. Mauris vitae ligula aliquam, volutpat urna nec, interdum eros. Sed accumsan nec ipsum ut aliquet. Suspendisse varius efficitur augue, ornare condimentum enim pulvinar sollicitudin. Suspendisse ut molestie lorem, pretium laoreet ex. Donec justo metus, sodales sit amet ante nec, tristique volutpat ligula.</p>
</section>

<section class="widgets abs">
  <h2 class="widget-title abs" style="left:70px;top:18px">Featured Auctions</h2>

  <div class="auction-card abs" style="left:70px;top:49px"><div class="photo" role="img" aria-label="Green farm tractor" style="background:linear-gradient(#9ec0e0,#4f7a32)"></div><div class="label">Nulla velit</div></div>
  <div class="auction-card abs" style="left:173px;top:49px"><div class="photo" role="img" aria-label="Cattle in a pasture" style="background:linear-gradient(#6f9d4a,#3d5e2a)"></div><div class="label">Nulla velit</div></div>
  <div class="auction-card abs" style="left:275px;top:49px"><div class="photo" role="img" aria-label="Brown cow on grass" style="background:linear-gradient(#7ea858,#6a4a34)"></div><div class="label">Nulla velit</div></div>

  <div class="auction-card abs" style="left:70px;top:162px"><div class="photo" role="img" aria-label="Compact tractor" style="background:linear-gradient(#c8d2da,#3e7a2c)"></div><div class="label">Nulla velit</div></div>
  <div class="auction-card abs" style="left:173px;top:162px"><div class="photo" role="img" aria-label="Two-storey house" style="background:linear-gradient(#5d9fd6,#d9b37c)"></div><div class="label">Nulla velit</div></div>
  <div class="auction-card abs" style="left:275px;top:162px"><div class="photo" role="img" aria-label="Large stone house" style="background:linear-gradient(#8fbbe2,#b4a68a)"></div><div class="label">Nulla velit</div></div>

  <div class="auction-card abs" style="left:70px;top:274px"><div class="photo" role="img" aria-label="Rows of solar panels" style="background:linear-gradient(#2a4a8e,#5a86c8)"></div><div class="label">Nulla velit</div></div>
  <div class="auction-card abs" style="left:173px;top:274px"><div class="photo" role="img" aria-label="Sheep grazing" style="background:linear-gradient(#7fb04a,#c9c8b8)"></div><div class="label">Nulla velit</div></div>
  <div class="auction-card abs" style="left:275px;top:274px"><div class="photo" role="img" aria-label="Tractor with hay wagon" style="background:linear-gradient(#6fb4e0,#d8c53a)"></div><div class="label">Nulla velit</div></div>

  <h2 class="widget-title abs" style="left:392px;top:18px">Latest News</h2>
  <div class="post-list abs" style="left:394px;top:43px;height:136px">
    <div class="post" style="top:9px"><div class="date"><span class="m">SEP</span><span class="d">17</span></div><p>Maecenas libero libero, mattis in augue porttitor, pretium volutpat massa. Nam ac tempus metus. Praesent enim risus, aliquet ac dolor sit amet, cursus elementum sem.</p></div>
    <div class="post" style="top:73px"><div class="date"><span class="m">SEP</span><span class="d">17</span></div><p>Maecenas libero libero, mattis in augue porttitor, pretium volutpat massa. Nam ac tempus metus. Praesent enim risus, aliquet ac dolor sit amet, cursus elementum sem.</p></div>
  </div>

  <h2 class="widget-title abs" style="left:392px;top:210px">Latest Events</h2>
  <div class="post-list abs" style="left:394px;top:235px;height:136px">
    <div class="post" style="top:9px"><div class="date"><span class="m">SEP</span><span class="d">17</span></div><p>Maecenas libero libero, mattis in augue porttitor, pretium volutpat massa. Nam ac tempus metus. Praesent enim risus, aliquet ac dolor sit amet, cursus elementum sem.</p></div>
    <div class="post" style="top:73px"><div class="date"><span class="m">SEP</span><span class="d">17</span></div><p>Maecenas libero libero, mattis in augue porttitor, pretium volutpat massa. Nam ac tempus metus. Praesent enim risus, aliquet ac dolor sit amet, cursus elementum sem.</p></div>
  </div>
</section>

<section class="newsletter abs">
  <h2>NEWS LETTER</h2>
  <div class="field" style="left:244px;width:166px">Name</div>
  <div class="field" style="left:415px;width:167px">Email ID</div>
  <div class="subscribe">Subscribe</div>
</section>

<footer class="site-footer abs">
  <div class="footer-nav"><span>Home</span><span>Auctions</span><span>Auction Services</span><span>Sellers</span><span>TR Kemble Livestock</span><span>About us</span><span>Contact us</span></div>
  <div class="footer-rule"></div>
  <div class="copyright">Copyright © 2014 T.R. Kemble,Inc. &nbsp;All rights reserved.</div>
  <div class="footer-brand">T.R. Kemble<br>Inc. / Auctioneers</div>
  <svg class="abs" style="left:190px;top:88px" width="104" height="22" viewBox="0 0 104 22">
    <circle cx="11" cy="11" r="10" fill="#3b5998"/>
    <circle cx="38" cy="11" r="10" fill="#f28a1e"/>
    <circle cx="64" cy="11" r="10" fill="#d63a2a"/>
    <circle cx="91" cy="11" r="10" fill="#5ea64a"/>
  </svg>
  <svg class="abs" style="left:354px;top:80px" width="138" height="36" viewBox="0 0 138 36">
    <rect x="0" y="10" width="48" height="16" rx="2" fill="#e8e8e8"/>
    <rect x="56" y="8" width="36" height="20" rx="2" fill="none" stroke="#bbb" stroke-width="1.5"/>
    <circle cx="119" cy="18" r="17" fill="#d8d8d8"/>
  </svg>
  <div class="footer-contact">4710 NC Hwy. 91, Cedar Ridge, NC 27000<br>Call : (555) 318-6402<br>E-mail : trkemble@trkemble-example.com</div>
</footer>
</body>
</html>
```